RW Framewell Inc Business cards

We need business cards using our existing logo but slightly modified. Right now the logo says RW Loadbearing Masonry. We want to keep the RW part of the design, but replace the Structural Concrete portion with "FRAMEWELL". Please see the attached file.
Ideally this would be a blank template so we can add Different Names, titles, and phone numbers later.
On the one side we want only the logo and on the other side the detail. I'm attaching an example for you to see.
Please reach out with any other questions. Our address and other details will be given out once we find a design we like.

Target Market(s)

Construction Industry

```html
<!DOCTYPE html>
<html lang="en">
<head>
<meta charset="utf-8">
<title>RW Framewell Inc – Business Cards</title>
<link rel="stylesheet" href="https://fonts.googleapis.com/css2?family=Roboto:wght@400;500;700&display=swap">
<style>
  :root {
    --page-bg: #e9edf3;
    --brand-blue: #2d5fa3;
    --brand-blue-deep: #1f4c8c;
    --card-white: #f7f7f6;
    --text-grey: #555a60;
    --rule-blue: #3a67a8;
    --icon-grey: #4a5a74;
  }
  * { box-sizing: border-box; margin: 0; padding: 0; }
  html, body {
    width: 1200px; height: 852px; overflow: hidden;
    background: var(--page-bg);
    font-family: "Roboto", Arial, sans-serif;
  }
  .sheet {
    position: relative; width: 1200px; height: 852px;
  }
  .card {
    position: absolute; top: 281px;
    width: 500px; height: 290px;
    border-radius: 22px;
    box-shadow: 0 6px 18px rgba(0,0,0,.18);
    overflow: hidden;
  }
  /* Logo side */
  .card--front {
    left: 70px;
    background: var(--brand-blue);
    display: flex; align-items: center; justify-content: center;
  }
  .wordmark {
    font-family: "Roboto", Arial, sans-serif;
    font-weight: 700;
    letter-spacing: 6px;
    white-space: nowrap;
  }
  .card--front .wordmark {
    font-size: 40px;
    color: var(--brand-blue-deep);
    text-shadow: none;
  }
  /* Detail side */
  .card--back {
    left: 630px;
    background: var(--card-white);
  }
  .card--back .wordmark {
    position: absolute; top: 44px; right: 40px;
    font-size: 30px; color: var(--brand-blue);
  }
  .rule {
    position: absolute; height: 1px; background: var(--rule-blue);
  }
  .rule--top { top: 104px; left: 40px; right: 30px; }
  .rule--name { top: 200px; left: 36px; width: 230px; }
  .address {
    position: absolute; top: 118px; right: 34px;
    text-align: right; font-size: 13px; line-height: 18px;
    color: var(--text-grey);
  }
  .edge-tab {
    position: absolute; left: -20px; top: 168px;
    width: 40px; height: 40px; border-radius: 50%;
    background: var(--brand-blue);
  }
  .person { position: absolute; left: 36px; top: 156px; }
  .person__name {
    font-size: 20px; font-weight: 700; color: var(--brand-blue);
  }
  .person__title {
    font-size: 13px; color: var(--text-grey); margin-top: 2px;
  }
  .contacts {
    position: absolute; left: 44px; top: 212px;
    list-style: none; font-size: 13px; color: var(--text-grey);
  }
  .contacts li {
    display: flex; align-items: center; gap: 12px; height: 20px;
  }
  .contacts svg { width: 12px; height: 12px; fill: var(--icon-grey); flex: none; }
</style>
</head>
<body>
<main class="sheet">
  <section class="card card--front" aria-label="Logo side">
    <span class="wordmark">RW FRAMEWELL</span>
  </section>

  <section class="card card--back" aria-label="Detail side">
    <span class="wordmark">RW FRAMEWELL</span>
    <div class="rule rule--top"></div>
    <p class="address">88 Timber Row, Oak Falls,<br>California, US 904512</p>

    <div class="edge-tab"></div>
    <div class="person">
      <p class="person__name">Alex RW Morgan</p>
      <p class="person__title">Managing Director</p>
    </div>
    <div class="rule rule--name"></div>

    <ul class="contacts">
      <li>
        <svg viewBox="0 0 12 12" aria-hidden="true"><path d="M2.5 1h2l1 2.6-1.3 1a6 6 0 0 0 3.2 3.2l1-1.3 2.6 1v2A1.5 1.5 0 0 1 9.5 11 8.5 8.5 0 0 1 1 2.5 1.5 1.5 0 0 1 2.5 1z"/></svg>
        555-010-0199
      </li>
      <li>
        <svg viewBox="0 0 12 12" aria-hidden="true"><path d="M1 2.5h10v7H1z M1.6 3 6 6.6 10.4 3" stroke="#f7f7f6" stroke-width=".9"/></svg>
        alex@framewellco.com
      </li>
      <li>
        <svg viewBox="0 0 12 12" aria-hidden="true"><circle cx="6" cy="6" r="5"/><path d="M1 6h10M6 1c-2.5 2.8-2.5 7.2 0 10M6 1c2.5 2.8 2.5 7.2 0 10" stroke="#f7f7f6" stroke-width=".8" fill="none"/></svg>
        www.framewellco.com
      </li>
    </ul>
  </section>
</main>
</body>
</html>
```